Social Media Graphics - Oakline Push REVISED

Create 6-7 individual social media graphics (square size) to encourage folks to join our online course called:

The Harvest Ledger Circle
How to Launch a Multi-Million Business From Scratch
Sign Up Today!

IMPORTANT: Make the largest and most prominent text on the graphic be: How to Launch a Multi-Million Business From Scratch

For the color scheme of the graphics, let's try a blue color palette; make sure the graphics appeal to both men and women

Make sure each graphic contains 1 of the 3 pics attached (crop pic as needed); and make sure one of the graphics is all TEXT only.

Target Market(s)

men and women looking to start a business

Industry/Entity Type

Entrepreneurship

Colors
0054AA
0677BA
7BADD7
CADEEF
E8F1F8

Requirements
Must have
• All the text and use the 3 pics provided; one graphic can be all text; Simple, modern design that's easy to read

```html
<!DOCTYPE html>
<html lang="en">
<head>
<meta charset="utf-8">
<title>The Harvest Ledger Circle – Social Graphics</title>
<link href="https://fonts.googleapis.com/css2?family=Questrial&family=Crimson+Text:wght@400;600&family=Russo+One&family=Great+Vibes&display=swap" rel="stylesheet">
<style>
  :root{
    --blue:#0054AA;
    --blue-mid:#0677BA;
    --blue-soft:#7BADD7;
    --blue-pale:#CADEEF;
    --blue-mist:#E8F1F8;
    --page:#dcdcdc;
    --light:#f2f2f4;
    --white:#ffffff;
    --ink:#222222;
    --blush:#f4dbe6;
  }
  *{margin:0;padding:0;box-sizing:border-box}
  html,body{width:1200px;height:833px;overflow:hidden;background:var(--page)}
  .sheet{position:relative;width:1200px;height:833px}
  .tile{position:absolute;width:360px;height:360px;overflow:hidden}
  .tile svg.bg{position:absolute;inset:0;width:360px;height:360px}
  .t1{left:31px;top:36px;background:var(--blue)}
  .t2{left:420px;top:36px;background:var(--light)}
  .t3{left:809px;top:36px;background:var(--blue)}
  .t4{left:31px;top:420px;background:var(--light)}
  .t5{left:420px;top:420px;background:#ebebf3}
  .t6{left:809px;top:420px;background:var(--blue)}
  .txt{position:absolute;white-space:nowrap}
  .sans{font-family:"Questrial",sans-serif}
  .serif{font-family:"Crimson Text",serif}
  .bold{font-family:"Russo One",sans-serif}
  .script{font-family:"Great Vibes",cursive}
  .pill{position:absolute;display:flex;align-items:center;white-space:nowrap}
  .pill-left{border-radius:0 12px 12px 0;background:var(--white);color:var(--blue)}
  .pill-round{border-radius:13px}

  /* tile 1 */
  .t1 .pill{left:0;top:84px;width:130px;height:22px;padding-left:13px;font-size:12px}
  .t1 .kicker{left:14px;top:128px;font-size:11px;color:var(--white)}
  .t1 .name{left:14px;top:146px;font-size:15px;color:var(--white);letter-spacing:.4px}
  .t1 .name2{left:14px;top:168px;font-size:11px;color:var(--white)}
  .t1 .pitch{left:14px;font-size:19px;color:var(--white);letter-spacing:.3px}

  /* tile 2 */
  .t2 .title{left:16px;top:20px;font-size:20px;color:var(--white);line-height:1}
  .t2 .title2{left:44px;top:46px;font-size:17px;color:var(--white);line-height:1}
  .t2 .pill{left:0;top:196px;width:125px;height:22px;padding-left:9px;background:var(--blue);color:var(--white);border-radius:0 12px 12px 0;font-size:14px}
  .t2 .pitch{left:9px;font-size:21px;line-height:1;color:#3a3a3a}
  .t2 .hl{color:var(--blue)}

  /* tile 3 */
  .t3 .pill{left:0;top:17px;width:121px;height:22px;padding-left:5px;font-size:11.5px}
  .t3 .badge{left:235px;top:22px;width:86px;height:86px;border-radius:50%;background:var(--white);display:flex;flex-direction:column;align-items:center;justify-content:center;font-size:8.5px;line-height:18px;color:var(--ink)}
  .t3 .badge b{font-weight:400;color:var(--blue)}
  .t3 .pitch{left:96px;top:270px;width:226px;text-align:center;font-size:15px;line-height:21px;color:var(--blue);white-space:normal}

  /* tile 4 */
  .t4 .scripttitle{left:0;top:214px;width:360px;text-align:center;font-size:21px;color:var(--blush)}
  .t4 .caps{left:0;width:360px;text-align:center;font-size:16px;color:var(--white);letter-spacing:.2px}
  .t4 .cta{left:0;top:318px;width:360px;text-align:center;font-size:21px;color:var(--blush)}

  /* tile 5 – text only */
  .t5 .title{left:0;top:10px;width:360px;text-align:center;font-size:14px;color:var(--white)}
  .t5 .title2{left:0;top:30px;width:360px;text-align:center;font-size:18px;font-weight:600;color:var(--white)}
  .t5 .pitch{left:0;width:360px;text-align:center;font-size:30px;line-height:1;color:var(--blue)}
  .t5 .pitch .dark{color:var(--ink)}
  .t5 .pill{left:120px;top:282px;width:120px;height:28px;justify-content:center;background:var(--blue);color:var(--white);font-size:15px;border-radius:14px;box-shadow:2px 2px 0 #0a2a55}

  /* tile 6 */
  .t6 .badge{left:40px;top:157px;width:114px;height:114px;border-radius:50%;background:var(--white);display:flex;flex-direction:column;align-items:center;justify-content:center;color:var(--ink);line-height:1.25}
  .t6 .badge .a{font-size:12px}
  .t6 .badge .b{font-size:14px;color:var(--blue)}
  .t6 .pitch{left:25px;font-size:17px;line-height:1;color:var(--white)}
  .t6 .pill{left:238px;top:309px;width:105px;height:24px;justify-content:center;background:var(--white);color:var(--blue);font-size:13px;box-shadow:2px 2px 0 #0a2a55}
</style>
</head>
<body>
<main class="sheet">

  <section class="tile t1">
    <svg class="bg" viewBox="0 0 360 360">
      <defs>
        <linearGradient id="ph1" x1="0" y1="0" x2="0" y2="1">
          <stop offset="0" stop-color="#c9b9a6"/><stop offset="1" stop-color="#6f6a66"/>
        </linearGradient>
      </defs>
      <path role="img" aria-label="Photo of the two course hosts speaking on stage, one holding a microphone"
            d="M71,0 C110,20 150,60 180,110 C205,150 190,220 215,270 C235,310 242,340 245,360 L360,360 L360,0 Z" fill="url(#ph1)"/>
    </svg>
    <div class="pill pill-left sans">SIGN UP TODAY!</div>
    <div class="txt sans kicker">THE</div>
    <div class="txt sans name">HARVEST LEDGER</div>
    <div class="txt sans name2">CIRCLE</div>
    <div class="txt sans pitch" style="top:214px">HOW TO LAUNCH A</div>
    <div class="txt sans pitch" style="top:244px">MULTI-MILLION</div>
    <div class="txt sans pitch" style="top:274px">BUSINESS FROM</div>
    <div class="txt sans pitch" style="top:304px">SCRATCH</div>
  </section>

  <section class="tile t2">
    <svg class="bg" viewBox="0 0 360 360">
      <defs>
        <linearGradient id="ph2" x1="0" y1="0" x2="1" y2="1">
          <stop offset="0" stop-color="#3a3e48"/><stop offset="1" stop-color="#2b2f3a"/>
        </linearGradient>
      </defs>
      <polygon points="0,0 360,360 300,360 0,60" fill="#fafafa" opacity=".7"/>
      <path d="M0,0 L250,0 L150,125 Q125,150 95,140 L0,95 Z" fill="var(--blue)"/>
      <polygon points="250,0 295,0 120,230 75,230" fill="var(--white)" opacity=".85"/>
      <path role="img" aria-label="Portrait photo of the two course hosts smiling, arms crossed"
            d="M292,0 L360,0 L360,270 L305,324 Q290,338 275,324 L148,200 Q135,180 150,160 Z" fill="url(#ph2)"/>
      <path d="M175,360 L225,318 Q235,310 245,318 L295,360 Z" fill="var(--blue)"/>
    </svg>
    <div class="txt serif title">The Harvest Ledger</div>
    <div class="txt serif title2">Circle</div>
    <div class="pill serif">Sign Up Today!</div>
    <div class="txt serif pitch" style="top:234px">How to Launch a</div>
    <div class="txt serif pitch hl" style="top:260px">Multi-Million</div>
    <div class="txt serif pitch" style="top:286px"><span class="hl">Business</span> From</div>
    <div class="txt serif pitch" style="top:312px">Scratch</div>
  </section>

  <section class="tile t3">
    <svg class="bg" viewBox="0 0 360 360">
      <defs>
        <linearGradient id="ph3" x1="0" y1="0" x2="0" y2="1">
          <stop offset="0" stop-color="#b04848"/><stop offset=".45" stop-color="#3a3e48"/><stop offset="1" stop-color="#1f2430"/>
        </linearGradient>
      </defs>
      <path d="M40,208 A146,146 0 0 1 240,32" fill="none" stroke="var(--white)" stroke-width="3"/>
      <path d="M310,100 A146,146 0 0 1 330,208" fill="none" stroke="var(--white)" stroke-width="3"/>
      <circle role="img" aria-label="Circular portrait photo of the two course hosts smiling" cx="184" cy="174" r="138" fill="url(#ph3)"/>
      <polygon points="92,263 326,263 330,322 160,322 110,348 100,322" fill="var(--white)"/>
    </svg>
    <div class="pill pill-left sans">SIGN UP TODAY!</div>
    <div class="txt sans badge"><span>THE <b>HARVEST</b></span><span>LEDGER CIRCLE</span></div>
    <div class="txt serif pitch">How to Launch a Multi-Million Business From Scratch</div>
  </section>

  <section class="tile t4">
    <svg class="bg" viewBox="0 0 360 360">
      <defs>
        <linearGradient id="ph4" x1="0" y1="0" x2="0" y2="1">
          <stop offset="0" stop-color="#cbbca8"/><stop offset="1" stop-color="#6a6660"/>
        </linearGradient>
      </defs>
      <path d="M327,0 A22,22 0 0 0 360,28" fill="none" stroke="#333" stroke-width="1"/>
      <circle cx="180" cy="132" r="106" fill="none" stroke="var(--blue)" stroke-width="3"/>
      <circle role="img" aria-label="Circular photo of the two course hosts presenting on stage" cx="180" cy="132" r="104" fill="url(#ph4)"/>
      <path d="M0,234 Q180,160 360,234 L360,360 L0,360 Z" fill="var(--blue)"/>
    </svg>
    <div class="txt script scripttitle">The Harvest Ledger Circle</div>
    <div class="txt bold caps" style="top:258px">HOW TO LAUNCH A MULTI-MILLION</div>
    <div class="txt bold caps" style="top:286px">BUSINESS FROM SCRATCH</div>
    <div class="txt script cta">Sign Up Today</div>
  </section>

  <section class="tile t5">
    <svg class="bg" viewBox="0 0 360 360">
      <polygon points="250,0 360,0 360,60 60,360 0,360 0,300" fill="#f4f4f8" opacity=".6"/>
      <circle cx="180" cy="-36" r="111" fill="var(--blue)"/>
      <path d="M310,330 l8,8 -8,8 M316,330 l8,8 -8,8 M322,330 l8,8 -8,8" fill="none" stroke="#888" stroke-width="1"/>
    </svg>
    <div class="txt serif title">The Harvest Ledger</div>
    <div class="txt serif title2">Circle</div>
    <div class="txt serif pitch" style="top:118px">How to Launch a</div>
    <div class="txt serif pitch dark" style="top:156px"><span class="dark">Multi-Million Business</span></div>
    <div class="txt serif pitch" style="top:194px">From Scratch</div>
    <div class="pill serif">Sign Up Today!</div>
  </section>

  <section class="tile t6">
    <svg class="bg" viewBox="0 0 360 360">
      <defs>
        <linearGradient id="ph6" x1="0" y1="0" x2="0" y2="1">
          <stop offset="0" stop-color="#cdbfae"/><stop offset="1" stop-color="#7a7268"/>
        </linearGradient>
      </defs>
      <rect role="img" aria-label="Photo of the two course hosts presenting on stage, one gesturing with a microphone" x="0" y="0" width="360" height="360" fill="url(#ph6)"/>
      <rect x="16" y="19" width="328" height="276" fill="none" stroke="var(--blue)" stroke-width="2"/>
      <polygon points="140,258 360,292 360,360 300,360" fill="var(--blue-pale)"/>
      <polygon points="0,190 150,262 350,360 0,360" fill="var(--blue)"/>
    </svg>
    <div class="txt serif badge"><span class="a">The</span><span class="b">Harvest Ledger</span><span class="a">Circle</span></div>
    <div class="txt serif pitch" style="top:290px">How to Launch a Multi-Million</div>
    <div class="txt serif pitch" style="top:318px">Business From Scratch</div>
    <div class="pill pill-round serif">Sign Up Today!</div>
  </section>

</main>
</body>
</html>
```